Stationary Set Rebrand for Brennick

We are a Canadian Distribution and Service Company that was established in 1969. Over the past 5 decades we have expanded our business and have warehouses across Canada. We specialize in adhesive tapes, adhesives, films, safety, warehouse, shipping, janitorial and packaging supplies.

We have updated our logo design and would like a new corporate branding identity that includes a new fresh Stationary Set (Business Cards, Letterhead, Letterhead MS Word, Envelope, Presentation Folders, Email Signatures, Notepad Covers, etc.)

Target Market(s)

Industrial Business Sector

Font styles to use
Sans Serif

Colors
0054AA
0677BA
7BADD7
CADEEF
E8F1F8
0094D4
00A9DD
6FCCEA
C7EBF8
E9F6FB
00AB8E
00BBA5
67D7C9
C6EFE9
E9F9F6
EB3D1F
EC4F4E
F09395
F8D3D4
FCEDEE

Requirements
Should not have
• Colors not too light, darker colours preferred

```html
<!DOCTYPE html>
<html lang="en">
<head>
<meta charset="utf-8">
<title>Brennick Business Card</title>
<link href="https://fonts.googleapis.com/css2?family=Open+Sans:wght@400;600;700&display=swap" rel="stylesheet">
<style>
  :root {
    --backdrop: #2b2b2b;
    --card-white: #ffffff;
    --card-black: #1e1e1e;
    --ink: #1f1f1f;
    --ink-soft: #5a5a5a;
    --rule: #6b6b6b;
    --accent-red: #d71920;
  }
  * { box-sizing: border-box; margin: 0; padding: 0; }
  html, body {
    width: 1200px; height: 900px; overflow: hidden;
    background: var(--backdrop);
    font-family: "Open Sans", Arial, sans-serif;
  }
  .sheet {
    position: relative; width: 1200px; height: 900px;
    display: flex; flex-direction: column; align-items: center; justify-content: center; gap: 50px;
  }
  .card {
    position: relative; width: 560px; height: 320px; overflow: hidden;
    box-shadow: 0 10px 30px rgba(0,0,0,.45);
  }
  .card--front { background: var(--card-white); }
  .card--back {
    background: var(--card-black);
    display: flex; align-items: center; justify-content: center;
  }
  .holder {
    position: absolute; left: 36px; top: 40px;
  }
  .holder__name {
    color: var(--accent-red); font-weight: 600; font-size: 22px; letter-spacing: .5px;
    text-transform: uppercase; line-height: 1.1;
  }
  .holder__title { color: var(--ink-soft); font-size: 15px; margin-top: 2px; }
  .divider {
    position: absolute; left: 36px; right: 40px; top: 112px;
    height: 1px; background: var(--rule);
  }
  .contacts {
    position: absolute; left: 36px; top: 126px; list-style: none;
    color: var(--ink-soft); font-size: 15px; line-height: 24px;
  }
  .contacts li { display: flex; align-items: center; gap: 8px; }
  .contacts svg { width: 13px; height: 13px; fill: var(--accent-red); flex: none; }
  .wordmark {
    font-weight: 700; color: var(--ink); font-size: 64px; letter-spacing: -1px; line-height: 1;
  }
  .card--front .wordmark { position: absolute; right: 40px; top: 30px; }
  .card--back .wordmark { color: var(--card-white); font-size: 80px; }
  .address {
    position: absolute; right: 40px; top: 196px; text-align: right;
    color: var(--ink-soft); font-size: 15px; line-height: 22px;
  }
  .edge-band { position: absolute; left: 0; bottom: 0; width: 560px; height: 16px; }
</style>
</head>
<body>
<main class="sheet">
  <section class="card card--front" aria-label="Business card front">
    <div class="holder">
      <h1 class="holder__name">Daniel Archer</h1>
      <p class="holder__title">Managing Director</p>
    </div>
    <div class="divider"></div>
    <ul class="contacts">
      <li><svg viewBox="0 0 16 16" aria-hidden="true"><path d="M3 1h3l1.5 4-2 1.2a9 9 0 0 0 4.3 4.3L11 8.5l4 1.5v3a2 2 0 0 1-2 2A12 12 0 0 1 1 3a2 2 0 0 1 2-2z"/></svg>044-987 654 321</li>
      <li><svg viewBox="0 0 16 16" aria-hidden="true"><path d="M1 3h14v10H1z M1 3l7 6 7-6" stroke="#fff" stroke-width="1"/></svg>hello@brennick.ca</li>
      <li><svg viewBox="0 0 16 16" aria-hidden="true"><circle cx="8" cy="8" r="7"/><path d="M1 8h14M8 1c3 3 3 11 0 14M8 1c-3 3-3 11 0 14" stroke="#fff" stroke-width="1" fill="none"/></svg>www.brennick.ca</li>
    </ul>
    <div class="wordmark">Brennick</div>
    <p class="address">Your Address, City<br>State, Zip 0000</p>
    <svg class="edge-band" viewBox="0 0 560 16" preserveAspectRatio="none" aria-hidden="true">
      <polygon points="0,0 170,0 162,16 0,16" fill="var(--card-black)"/>
      <polygon points="182,0 560,0 560,16 174,16" fill="var(--accent-red)"/>
    </svg>
  </section>

  <section class="card card--back" aria-label="Business card back">
    <div class="wordmark">Brennick</div>
  </section>
</main>
</body>
</html>
```